Veltrano.co - Polar Expeditions Specialists

We need a modern, visually striking business card for Veltrano.co, a company specialized in selling expedition cruises to the most remote regions on Earth, with a focus on the Arctic and Antarctica. The design should instantly communicate that the cardholder is an expert in polar travel. Use clean, premium aesthetics with cool tones like icy blue and white, possibly incorporating polar imagery (ice, glaciers, penguins, etc.)

Attached the logo

Contact Information for Business Card

Feels high-end and trustworthy.. Visually memorable — encourages people to keep it

Colors
0054AA
0677BA
7BADD7
CADEEF
E8F1F8

Requirements
Must have
• ice, glaciers, penguins, montains
Nice to have
• modern, transparente,

```html
<!DOCTYPE html>
<html lang="en">
<head>
<meta charset="utf-8">
<title>Veltrano.co Business Card</title>
<link href="https://fonts.googleapis.com/css2?family=Poppins:wght@400;500;600&display=swap" rel="stylesheet">
<style>
  :root {
    --bg: #3a3a3a;
    --bg-dark: #2c2c2c;
    --card: #141414;
    --ice-blue: #3a80c9;
    --ice-light: #7badd7;
    --ice-pale: #cadeef;
    --white: #f2f2f2;
    --gloss: #8a8a8a;
    --gloss-dark: #262626;
  }
  * { margin: 0; padding: 0; box-sizing: border-box; }
  html, body { width: 1200px; height: 791px; overflow: hidden; }
  body {
    background: radial-gradient(ellipse at 50% 40%, var(--bg) 0%, var(--bg-dark) 100%);
    font-family: "Poppins", sans-serif;
    position: relative;
  }
  .card {
    position: absolute;
    top: 240px;
    width: 540px;
    height: 311px;
    background: var(--card);
    border-bottom: 3px solid var(--ice-blue);
    box-shadow: 0 18px 40px rgba(0,0,0,0.45);
  }
  .card--front { left: 45px; }
  .card--back { left: 615px; }

  .brand {
    position: absolute;
    display: flex;
    align-items: center;
    gap: 16px;
  }
  .brand__art {
    width: 78px;
    height: 78px;
    flex: none;
    background: linear-gradient(160deg, var(--ice-pale) 0%, var(--ice-light) 45%, var(--ice-blue) 100%);
  }
  .brand__name {
    font-weight: 500;
    font-size: 38px;
    line-height: 1.05;
    color: var(--ice-blue);
  }
  .brand__tagline {
    font-weight: 500;
    font-size: 12px;
    color: var(--ice-blue);
    letter-spacing: 0.3px;
    margin-top: 4px;
  }
  .card--front .brand { left: 110px; top: 44px; }

  .holder {
    position: absolute;
    left: 38px;
    top: 205px;
    text-align: right;
    width: 222px;
  }
  .holder__name {
    font-weight: 600;
    font-size: 19px;
    color: var(--ice-blue);
    letter-spacing: 0.5px;
    white-space: nowrap;
  }
  .holder__title {
    font-size: 15px;
    color: var(--white);
  }
  .divider {
    position: absolute;
    left: 282px;
    top: 196px;
    width: 1px;
    height: 70px;
    background: var(--ice-blue);
  }
  .contacts {
    position: absolute;
    left: 304px;
    top: 196px;
    list-style: none;
  }
  .contacts li {
    display: flex;
    align-items: center;
    gap: 8px;
    font-size: 13px;
    color: var(--white);
    line-height: 23px;
    white-space: nowrap;
  }
  .contacts svg { width: 12px; height: 12px; fill: var(--ice-blue); flex: none; }

  .card--back .brand { left: 92px; top: 104px; }
  .card--back .brand__art {
    background: linear-gradient(160deg, #2a2a2a 0%, #0c0c0c 100%);
  }
  .card--back .brand__name { color: var(--gloss); }
  .card--back .brand__tagline { color: var(--gloss); }
</style>
</head>
<body>
  <section class="card card--front">
    <div class="brand">
      <div class="brand__art" role="img" aria-label="Polar bear and ice illustration in icy blue tones"></div>
      <div>
        <div class="brand__name">Veltrano.co</div>
        <div class="brand__tagline">Polar Expeditions Specialists</div>
      </div>
    </div>
    <div class="holder">
      <div class="holder__name">MARCUS LINDQVIST</div>
      <div class="holder__title">President</div>
    </div>
    <div class="divider"></div>
    <ul class="contacts">
      <li>
        <svg viewBox="0 0 24 24" aria-hidden="true"><path d="M6.6 10.8a15.1 15.1 0 0 0 6.6 6.6l2.2-2.2c.3-.3.7-.4 1-.2 1.1.4 2.3.6 3.6.6.6 0 1 .4 1 1V20c0 .6-.4 1-1 1A17 17 0 0 1 3 4c0-.6.4-1 1-1h3.5c.6 0 1 .4 1 1 0 1.3.2 2.5.6 3.6.1.3 0 .7-.2 1z"/></svg>
        555-018-2047
      </li>
      <li>
        <svg viewBox="0 0 24 24" aria-hidden="true"><path d="M2 5h20v14H2z"/><path d="M2 5l10 7 10-7" fill="none" stroke="#141414" stroke-width="2"/></svg>
        marcuslind@veltrano.co
      </li>
      <li>
        <svg viewBox="0 0 24 24" aria-hidden="true"><circle cx="12" cy="12" r="10"/></svg>
        www.veltrano.co
      </li>
    </ul>
  </section>

  <section class="card card--back">
    <div class="brand">
      <div class="brand__art" role="img" aria-label="Polar bear and ice illustration in gloss black"></div>
      <div>
        <div class="brand__name">Veltrano.co</div>
        <div class="brand__tagline">Polar Expeditions Specialists</div>
      </div>
    </div>
  </section>
</body>
</html>
```